"Tidewater Sleeve" - Envelope Package for 3 Small Pamphlets/Tracts

We need a design for an envelope package that will be folded to fit 3 small tracts/pamphlets. The final product will be paper that is simply folded - not glued or stapled. The tracts/pamphlets themselves are the ones that can be found at www.briskcanada.ca/literature - they don't need to be designed as we already have them in print. We just want a package/envelope to put them in so we can hand them out in a creative way.

We are looking for a few different ideas to choose from - which is why we are coming to you! Attached is a design brief that outlines the desired format and pictures of mocked-finished product. Also attached is the "G" (NORVA logo). One of the pictures will provide you with the final product measurement in millimetres. You will have to add safety margins for full bleed to send to the printer. This needs to be designed in Photoshop or Illustrator. Photoshop is preferred.

Although I like the white background because it looks clean, please also provide a darker background to see if the "wallet" effect would work. (I am talking about the outside of the package. the inside should remain white.)

I like the concept of the icons for body and mind, but the icon for "spirit" should be something like a generic sunrise, sunset or peaceful lake.

You will notice that there are "folding" numbers inside the attached mockup picture. We would like them to be nicely designed on the final product so that people know how to fold the envelope, but those numbers should be hidden behind the flaps/pamphlets once the 3 pamphlets are in and the product is fully folded. We would also like to have light grey dotted lines to know where to fold on the inside of the package.

On the centre back panel is where you have the question that states "Know someone who needs healing?"

```html
<!DOCTYPE html>
<html lang="en">
<head>
<meta charset="utf-8">
<title>Tidewater Sleeve – Envelope Die Layout</title>
<link rel="stylesheet" href="https://fonts.googleapis.com/css2?family=Montserrat:wght@300;800&display=swap">
<style>
  :root {
    --paper: #ffffff;
    --ink: #111111;
    --crop: #1a1a1a;
    --white: #ffffff;
    --brand-green: #7cf222;
  }
  * { margin: 0; padding: 0; box-sizing: border-box; }
  html, body { width: 1200px; height: 861px; overflow: hidden; background: var(--paper); }
  .sheet { position: relative; width: 1200px; height: 861px; font-family: "Montserrat", sans-serif; }
  .die { position: absolute; inset: 0; }

  .flap-label {
    position: absolute; top: 156px; width: 300px; margin-left: -150px;
    text-align: center; font-weight: 300; font-size: 52px; line-height: 1;
    color: var(--white); transform: rotate(180deg);
  }
  .flap-label--body { left: 318px; }
  .flap-label--mind { left: 608px; }
  .flap-label--spirit { left: 903px; }

  .headline {
    position: absolute; left: 455px; width: 306px; top: 290px;
    text-align: center; font-weight: 800; font-size: 46px; line-height: 44px;
    color: var(--ink); letter-spacing: -0.5px;
  }
  .headline__accent { color: var(--white); }

  .brand-block {
    position: absolute; left: 753px; top: 240px; width: 123px; height: 52px;
    background: var(--brand-green); display: flex; align-items: center; justify-content: flex-end;
    padding-right: 10px;
  }
  .brand-block__name { font-weight: 800; font-size: 20px; color: var(--white); letter-spacing: 0.5px; }

  .product-title {
    position: absolute; left: 760px; width: 286px; top: 372px;
    text-align: center; font-weight: 800; font-size: 44px; line-height: 44px; letter-spacing: -0.5px;
  }
  .product-title__first { color: var(--white); display: block; }
  .product-title__second { color: var(--ink); display: block; }

  .icon { position: absolute; width: 63px; height: 63px; border-radius: 9px; }
  .icon--small { width: 50px; height: 50px; border-radius: 7px; top: 661px; }
  .icon--row { top: 560px; }
  .icon--body { background: linear-gradient(180deg, #c9d8ea 0%, #f6c35a 55%, #ff9a1a 80%, #3a2a1a 100%); }
  .icon--mind { background: radial-gradient(circle at 50% 45%, #ff7a3c 0%, #4f55e0 45%, #1530b8 100%); }
  .icon--spirit { background: linear-gradient(180deg, #6b84a8 0%, #f0c27a 40%, #5e7ea3 60%, #2b3f5c 100%); }
  .icon--flip { transform: rotate(180deg); }
</style>
</head>
<body>
<main class="sheet">
  <svg class="die" width="1200" height="861" viewBox="0 0 1200 861">
    <defs>
      <linearGradient id="envelope-fill" x1="0" y1="0.2" x2="1" y2="0.5">
        <stop offset="0" stop-color="#ff5510"/>
        <stop offset="0.45" stop-color="#ff3a08"/>
        <stop offset="0.7" stop-color="#e82405"/>
        <stop offset="0.9" stop-color="#b31804"/>
        <stop offset="1" stop-color="#8e1204"/>
      </linearGradient>
      <clipPath id="envelope-clip">
        <path d="M180 142 L452 142 L457 210 L458 142 L757 142 L758 210 L764 142 L1027 142 L1045 210 L1048 210 L1048 592 L1125 592 L1125 649 L1048 649 L1048 658 L1045 658 L1027 727 L764 727 L758 658 L757 727 L458 727 L457 658 L452 727 L180 727 L162 658 L159 658 L159 649 L84 649 L84 592 L159 592 L159 210 L162 210 Z"/>
      </clipPath>
    </defs>
    <g clip-path="url(#envelope-clip)" role="img" aria-label="Background artwork: flowing orange and red abstract waves">
      <rect x="80" y="140" width="1050" height="590" fill="url(#envelope-fill)"/>
    </g>
    <g stroke="var(--crop)" stroke-width="0.8" fill="none" aria-hidden="true">
      <path d="M159 112 V142 M458 112 V142 M757 112 V142 M1048 112 V142"/>
      <path d="M159 727 V756 M458 727 V756 M757 727 V756 M1048 727 V756"/>
      <path d="M130 142 H159 M1048 142 H1077 M130 219 H159 M1048 219 H1077 M130 727 H159 M1048 727 H1077"/>
      <path d="M52 592 H82 M52 649 H82 M1127 592 H1155 M1127 649 H1155"/>
    </g>
  </svg>

  <div class="flap-label flap-label--body">Body</div>
  <div class="flap-label flap-label--mind">Mind</div>
  <div class="flap-label flap-label--spirit">Spirit</div>

  <div class="brand-block"><span class="brand-block__name">NORVA</span></div>

  <h1 class="headline">Know<br>someone<br>who<br>needs<br><span class="headline__accent">Healing?</span></h1>

  <h2 class="product-title"><span class="product-title__first">Tidewater</span><span class="product-title__second">Sleeve</span></h2>

  <div class="icon icon--row icon--body" style="left:483px" role="img" aria-label="Body icon: runner at sunset"></div>
  <div class="icon icon--row icon--mind" style="left:572px" role="img" aria-label="Mind icon: glowing brain in profile"></div>
  <div class="icon icon--row icon--spirit" style="left:662px" role="img" aria-label="Spirit icon: mountain lake at sunrise"></div>
  <div class="icon icon--row icon--body" style="left:777px" role="img" aria-label="Body icon: runner at sunset"></div>
  <div class="icon icon--row icon--mind" style="left:866px" role="img" aria-label="Mind icon: glowing brain in profile"></div>
  <div class="icon icon--row icon--spirit" style="left:956px" role="img" aria-label="Spirit icon: mountain lake at sunrise"></div>

  <div class="icon icon--small icon--body icon--flip" style="left:277px" role="img" aria-label="Body icon on flap: runner at sunset"></div>
  <div class="icon icon--small icon--mind icon--flip" style="left:580px" role="img" aria-label="Mind icon on flap: glowing brain"></div>
  <div class="icon icon--small icon--spirit icon--flip" style="left:872px" role="img" aria-label="Spirit icon on flap: mountain lake"></div>
</main>
</body>
</html>
```